Technical Communications firm needs an article turned into a white paper

We want to redesign a 3-part blog series into a white paper that we can print for a conference. I've consolidated the three posts into the attached Word document.

We are looking for a light, easy to read design. Good use of graphics to support the message. I've added the graphics we used in the original post.

You can view them at
http://www.brightquillpages.com/blog/are-you-satisfied-with-your-dita-solution/

Target Market(s)

Product managers from High-tech, Finance, and Medical industries.

Industry/Entity Type

Information Technology

Colors

Designer to choose colors to be used in the design.

Requirements
Must have
• Must be modern, light, easy to read and slick design. Try to incorporate the graphics provided, but feel free to add more. Must retain the lists and tables.
• Must align with our website/brand.
• Must be easy to read. So not too busy.
• Please move all footnotes to endnotes. You'll need to rework the numbering.
Nice to have
• Awesome coverpage.
Should not have
• Hokey clipart. Not too heavy or hard to read.

```html
<!DOCTYPE html>
<html lang="en">
<head>
<meta charset="utf-8">
<title>Governance Strategies – White Paper Page 13</title>
<link rel="stylesheet" href="https://fonts.googleapis.com/css2?family=Carlito:wght@400;700&family=Open+Sans:wght@700&display=swap">
<style>
  :root {
    --navy: #1c1a9a;
    --cyan: #14a8e0;
    --ink: #2b2b2b;
    --rule: #9fc6e0;
    --paper: #ffffff;
  }
  html, body { margin: 0; padding: 0; overflow: hidden; }
  body { width: 927px; height: 1200px; background: var(--paper); }
  .page {
    position: relative; width: 927px; height: 1200px; overflow: hidden;
    background: var(--paper);
    font-family: "Carlito", "Calibri", sans-serif; color: var(--ink);
  }
  .brand { position: absolute; left: 84px; top: 62px; display: flex; align-items: center; gap: 12px; }
  .brand-mark { width: 62px; height: 62px; border-radius: 50%; background: var(--cyan); flex: none; }
  .brand-name {
    font-family: "Carlito", "Calibri", sans-serif; font-weight: 700; font-size: 27px;
    line-height: 25px; color: var(--navy); letter-spacing: 0.3px;
  }
  .spine { position: absolute; left: 110px; top: 142px; width: 3px; height: 918px; background: var(--navy); }
  .page-label {
    position: absolute; left: 744px; top: 70px; width: 126px; height: 28px;
    border-top: 1px solid var(--rule); border-bottom: 1px solid var(--rule);
    font-family: "Open Sans", sans-serif; font-weight: 700; font-size: 14px; color: var(--navy);
    display: flex; align-items: center; justify-content: center; letter-spacing: 0.5px;
  }
  .content { position: absolute; left: 178px; top: 181px; width: 692px; font-size: 16px; line-height: 22.4px; }
  .content p { margin: 0; text-align: justify; }
  .content sup { font-size: 10px; line-height: 0; }
  .carry { text-align: center !important; line-height: 18.4px; }
  .indent { text-indent: 28px; margin-top: 1px !important; }
  .section-title {
    margin: 31px 0 4px; text-align: center; font-family: "Open Sans", sans-serif;
    font-weight: 700; font-size: 31px; line-height: 40px; color: var(--navy);
    text-decoration: underline; text-decoration-thickness: 2px; text-underline-offset: 4px;
  }
  .benefits { list-style: none; margin: 26px 0 26px 86px; padding: 0; }
  .benefits li { position: relative; padding-left: 23px; line-height: 24.4px; }
  .benefits li::before {
    content: ""; position: absolute; left: 0; top: 10px; width: 5px; height: 5px;
    border-radius: 50%; background: var(--navy);
  }
  .gap { margin-top: 2px !important; }
  .footer-band {
    position: absolute; left: 106px; top: 1072px; width: 762px; height: 12px;
    border-radius: 6px; background: linear-gradient(90deg, var(--navy), var(--cyan));
  }
</style>
</head>
<body>
<div class="page">
  <div class="brand">
    <span class="brand-mark"></span>
    <span class="brand-name">BRIGHTQUILL<br>PAGES</span>
  </div>
  <div class="spine"></div>
  <div class="page-label">PAGE&nbsp; 13</div>

  <main class="content">
    <p class="carry">still only an experimental stage. You may not want to be locked into any long-term<br>commitments to one software vendor. Where possible, consider using subscription pricing<br>and a hosted solution at least until the pilot has proven to be successful.</p>
    <p class="indent">Once in production, consider conducting regular experiments on a staging server that remains isolated from your production systems. These experiments should examine new product features, validate new releases, and verify patches and fixes. Use experiments to test new authoring techniques and publishing solutions before going live with them to production.</p>

    <h2 class="section-title">Governance Strategies</h2>
    <p>Good governance is the key to scalability and sustainability of your program. When moving to a sophisticated, collaborative authoring solution, you need everyone playing by a common set of rules and guidelines. You need a strategy that addresses the needs of the business while catering to the needs of the team members responsible for carrying out the work. Governance needs to fit into the overall corporate strategy for managing its information assets. If executed well, you should see benefits<sup>4</sup> such as a</p>

    <ul class="benefits">
      <li>stable technology stack for authoring and publishing</li>
      <li>stable funding for skills development</li>
      <li>better opportunities for leveraging content from other departments</li>
      <li>better opportunities for others to reuse your content, and</li>
      <li>better opportunities for improvement and innovation.</li>
    </ul>

    <p>In 2015, Brightquill Pages commissioned a study with InfoStandards.org entitled Innovating Content Creation and Reuse<sup>5</sup>. This study polled more than 300 organizations from around the world about their content creation practices and technology. When respondents were asked about content standards in place to manage content creation, 16% indicated there are strict standards in place, while 47% acknowledged there is something there, but not strictly followed. For 37% the indication was that there is little to no use of standards in any form.</p>
    <p class="gap">Information Governance is the rocket fuel that empowers effective collaboration within and across teams and departments. Its purpose is to give everyone a voice in the future of the program and manage change across the enterprise. Good governance can be an important differentiator for your company.</p>
  </main>

  <div class="footer-band" role="img" aria-label="Decorative footer border in navy and cyan"></div>
</div>
</body>
</html>
```